Need a stunning home page for Car rental company

For a client, I need a slick and sumber home page design. It is a small, local car rental company, with a handful of cars available for rent.
Selling points: affordable lease, availability, always clean cars
The design should be:
- flat and modern
- no, or very few animations/sliders
- CTA: booking form for renting a car.
- 3 featured cars with images and facts (see website) with button to read more about the car.
- fullscreen background video can be an option
- main colour: #efba01
The site is under construction here:
http://solvikutleie.hammerlia.no/
Delivery requirements:
I need a layered & well organised PSD file delivered.

```html
<!DOCTYPE html>
<html lang="no">
<head>
<meta charset="utf-8">
<title>Solvik Utleie – Hjem</title>
<link href="https://fonts.googleapis.com/css2?family=Open+Sans:wght@400;600;700&display=swap" rel="stylesheet">
<style>
:root{
  --brand:#efba01;
  --brand-dark:#d9a400;
  --ink:#333;
  --muted:#777;
  --line:#e2e2e2;
  --panel:#f4f4f4;
  --field:#e9e9e9;
  --footer:#ededed;
  --bottom:#2b2b2b;
  --white:#fff;
}
*{box-sizing:border-box;margin:0;padding:0}
html,body{width:1200px;height:2247px;overflow:hidden}
body{font-family:"Open Sans",Arial,sans-serif;color:var(--ink);background:var(--white);position:relative}
.abs{position:absolute}
/* header */
.site-header{position:absolute;left:0;top:0;width:1200px;height:108px;background:var(--white)}
.brand{position:absolute;left:102px;top:32px;display:flex;align-items:center;gap:12px}
.brand-mark{width:18px;height:18px;background:var(--brand)}
.brand-name{font-size:34px;font-weight:700;color:#6d6d6d;letter-spacing:1px;text-transform:uppercase}
.search-btn{position:absolute;left:743px;top:40px;width:34px;height:34px;border-radius:50%;background:#6f6f6f}
.divider-v{position:absolute;top:30px;width:1px;height:52px;background:var(--line)}
.call{position:absolute;left:814px;top:35px}
.call small{display:block;font-size:13px;color:var(--muted)}
.call strong{display:block;font-size:22px;font-weight:600;color:var(--brand);line-height:26px}
.call svg{position:absolute;left:128px;top:12px}
.account-btn{position:absolute;left:1003px;top:41px;width:98px;height:32px;background:var(--brand);color:var(--white);font-size:12px;font-weight:600;border-radius:3px;display:flex;align-items:center;justify-content:center}
/* nav */
.main-nav{position:absolute;left:0;top:108px;width:1200px;height:46px;background:linear-gradient(#f6c21a,#e4ad00)}
.main-nav a{position:absolute;top:0;height:46px;line-height:46px;font-size:14px;font-weight:600;color:var(--white);text-decoration:none;text-transform:uppercase}
.main-nav a.active{background:#6b6b6b;padding:0 32px;left:100px}
/* hero */
.hero{position:absolute;left:0;top:154px;width:1200px;height:443px;background:linear-gradient(180deg,#44709f 0%,#7b9ab8 45%,#9a8676 72%,#5a4a42 100%)}
.hero-kicker{position:absolute;left:130px;top:52px;font-size:25px;color:var(--white)}
.hero-title{position:absolute;left:128px;top:78px;font-size:56px;font-weight:600;color:var(--white)}
.slide-arrow{position:absolute;top:200px;width:24px;height:44px;background:rgba(60,60,60,.85)}
.slide-arrow.left{left:0;border-radius:0 22px 22px 0}
.slide-arrow.right{right:0;border-radius:22px 0 0 22px}
/* booking */
.booking{position:absolute;left:810px;top:165px;width:291px;height:422px;background:var(--white);padding:0 28px}
.booking h2{font-size:32px;font-weight:600;color:var(--brand);margin:8px 0 0 -12px;line-height:40px}
.field{position:absolute;left:19px;width:254px;height:36px;background:var(--field);border-radius:3px;font-size:13px;color:#8a8a8a;padding-left:17px;line-height:36px}
.field.half{width:118px;font-size:11px;padding-left:12px}
.field.select{font-size:11px}
.field svg{position:absolute;right:12px;top:12px}
.lbl{position:absolute;left:19px;font-size:13px;color:#555}
.btn{display:flex;align-items:center;justify-content:center;background:linear-gradient(#f4c315,#e2a900);color:#3a2c00;font-size:13px;border-radius:3px}
/* welcome */
.welcome{position:absolute;left:0;top:597px;width:1200px;height:205px;text-align:center}
.welcome h1{margin-top:44px;font-size:26px;font-weight:600;color:var(--brand)}
.welcome p{width:830px;margin:14px auto 0;font-size:14px;line-height:24px;color:#888}
/* offers */
.offers{position:absolute;left:0;top:802px;width:1200px;height:708px;background:var(--panel)}
.offers h2{text-align:center;margin-top:45px;font-size:26px;font-weight:600;color:var(--brand)}
.car-card{position:absolute;top:105px;width:314px;height:553px;background:var(--white);border-top:4px solid var(--brand);box-shadow:0 1px 3px rgba(0,0,0,.08)}
.car-photo{height:183px}
.car-card h3{position:absolute;left:20px;top:201px;font-size:19px;font-weight:600;color:var(--brand)}
.price{position:absolute;left:20px;top:229px;font-size:14px;color:#666}
.price b{color:var(--ink);font-size:15px}
.car-card hr{position:absolute;left:20px;top:267px;width:282px;border:0;border-top:1px solid var(--line)}
.specs{position:absolute;left:20px;top:280px;font-size:13px;color:#666;border-collapse:collapse}
.specs td{height:29.2px;padding:0}
.specs td:first-child{width:149px}
.car-card .btn{position:absolute;left:20px;top:491px;width:88px;height:35px}
/* features */
.features{position:absolute;left:0;top:1510px;width:1200px;height:132px}
.feature{position:absolute;top:48px;display:flex;align-items:center;gap:16px;font-size:16px;color:#333;line-height:22px}
/* video */
.video{position:absolute;left:0;top:1642px;width:1200px;height:366px;background:linear-gradient(180deg,#16202d 0%,#0d1520 55%,#05080d 100%)}
.play{position:absolute;left:570px;top:156px;width:60px;height:60px;border-radius:50%;background:linear-gradient(#fafafa,#c9c9c9)}
/* footer */
.site-footer{position:absolute;left:0;top:2008px;width:1200px;height:180px;background:var(--footer)}
.site-footer h4{position:absolute;top:24px;font-size:17px;font-weight:400;color:var(--brand)}
.site-footer a{position:absolute;font-size:12px;color:#444;text-decoration:none}
.fsep{position:absolute;top:26px;width:1px;height:120px;background:#d4d4d4}
.news-text{position:absolute;left:617px;top:60px;width:250px;font-size:12px;line-height:20px;color:#777}
.email{position:absolute;left:617px;top:105px;width:243px;height:36px;background:var(--white);border:1px solid #ddd;border-radius:4px;font-size:12px;color:#444;padding-left:13px;line-height:34px}
.email .btn{position:absolute;right:-2px;top:-1px;width:66px;height:36px;font-size:12px;color:var(--white);border-radius:3px}
.social{position:absolute;top:60px;width:32px;height:32px;border-radius:50%}
.bottom-bar{position:absolute;left:0;top:2188px;width:1200px;height:59px;background:var(--bottom);text-align:center;line-height:59px;font-size:12px;color:#aaa}
</style>
</head>
<body>

<header class="site-header">
  <div class="brand"><span class="brand-mark"></span><span class="brand-name">Solvik Utleie</span></div>
  <div class="search-btn"><svg width="34" height="34" viewBox="0 0 34 34"><circle cx="15" cy="15" r="6" fill="none" stroke="#fff" stroke-width="2"/><line x1="19.5" y1="19.5" x2="24" y2="24" stroke="#fff" stroke-width="2.5" stroke-linecap="round"/></svg></div>
  <div class="divider-v" style="left:793px"></div>
  <div class="call"><small>Spørsmål? Ring oss</small><strong>91234560</strong>
    <svg width="20" height="20" viewBox="0 0 20 20"><path d="M4 2l4 1 1 4-2 1.5c1 2.5 3 4.5 5.5 5.5L14 12l4 1 1 4c-1 1.5-3 2-4.5 1.5C9 17 3 11 2.5 5.5 2 4 3 2.5 4 2z" fill="none" stroke="#efba01" stroke-width="1.6"/></svg></div>
  <div class="divider-v" style="left:982px"></div>
  <div class="account-btn">My Account</div>
</header>

<nav class="main-nav">
  <a class="active" href="#">Hjem</a>
  <a href="#" style="left:229px">Bilparken vår</a>
  <a href="#" style="left:404px">Tjenester</a>
  <a href="#" style="left:543px">Kontakt oss</a>
  <a href="#" style="left:707px">Blog</a>
  <a href="#" style="left:811px">Page templates</a>
  <a href="#" style="left:994px">About us</a>
</nav>

<section class="hero" role="img" aria-label="Photo of a dark sedan on an open road under a blue evening sky">
  <div class="hero-kicker">Lei en varebil med eller uten</div>
  <div class="hero-title">Driver</div>
  <div class="slide-arrow left"><svg width="24" height="44"><path d="M8 17l5 5-5 5" fill="none" stroke="#fff" stroke-width="2.5"/></svg></div>
  <div class="slide-arrow right"><svg width="24" height="44"><path d="M15 17l-5 5 5 5" fill="none" stroke="#fff" stroke-width="2.5"/></svg></div>
</section>

<form class="booking">
  <h2>Rent a Car</h2>
  <div class="field" style="top:60px">Name</div>
  <div class="field" style="top:105px">City</div>
  <div class="lbl" style="top:158px">From</div>
  <div class="lbl" style="top:158px;left:154px">To</div>
  <div class="field half" style="top:180px">dd/mm/yyyy<svg width="16" height="14"><rect x="0.5" y="0.5" width="15" height="13" fill="none" stroke="#777"/><path d="M0 4h16M4 4v10M8 4v10M12 4v10M0 8h16M0 11h16" stroke="#777" stroke-width=".8"/></svg></div>
  <div class="field half" style="top:180px;left:154px">dd/mm/yyyy<svg width="16" height="14"><rect x="0.5" y="0.5" width="15" height="13" fill="none" stroke="#777"/><path d="M0 4h16M4 4v10M8 4v10M12 4v10M0 8h16M0 11h16" stroke="#777" stroke-width=".8"/></svg></div>
  <div class="lbl" style="top:233px">Car Type</div>
  <div class="field select" style="top:253px">Select<svg width="14" height="10"><path d="M0 1h14L7 9z" fill="#888"/></svg></div>
  <div class="lbl" style="top:306px">Driver</div>
  <div class="field select" style="top:328px">No, Thanks<svg width="14" height="10"><path d="M0 1h14L7 9z" fill="#888"/></svg></div>
  <div class="btn abs" style="left:189px;top:375px;width:84px;height:33px">Book Now</div>
</form>

<section class="welcome">
  <h1>Velkommen til Solvik Utleie – Hammerlia</h1>
  <p>Solvik Utleie er en bilpark på Hammerlia, og leier ut varebiler og personbiler til deg som trenger en ekstrabil til flytting, ferie, bytur eller hva det måtte være. Vi er uslåelige på service, og mest sannsynlig også på pris. Og du kan stole på at bilen du får fra oss er både ren og pen!</p>
</section>

<section class="offers">
  <h2>Våre leietilbud</h2>

  <article class="car-card" style="left:100px">
    <div class="car-photo" role="img" aria-label="Photo of a white cargo van parked outdoors" style="background:linear-gradient(180deg,#b8c2cc 0%,#e1e3e5 50%,#8f8e8a 100%)"></div>
    <h3>Varebilen</h3>
    <div class="price">Pris per døgn <b>kr 600</b></div>
    <hr>
    <table class="specs">
      <tr><td>Biltype</td><td>Varebil</td></tr>
      <tr><td>Maks. pers.</td><td>2</td></tr>
      <tr><td>Ant. dører</td><td>5</td></tr>
      <tr><td>Min. sjåføralder</td><td>21</td></tr>
      <tr><td>Girtype</td><td>Manuell</td></tr>
      <tr><td>Klimaanlegg?</td><td>Ja</td></tr>
      <tr><td>Ubegrenset km?</td><td>Nei</td></tr>
    </table>
    <div class="btn">Book Now</div>
  </article>

  <article class="car-card" style="left:444px">
    <div class="car-photo" role="img" aria-label="Photo of an orange sports car under a blue sky" style="background:linear-gradient(180deg,#4f84bb 0%,#8aa6c0 45%,#c98a3a 70%,#6b4a2a 100%)"></div>
    <h3>Varebilen</h3>
    <div class="price">Pris per døgn <b>kr 600</b></div>
    <hr>
    <table class="specs">
      <tr><td>Biltype</td><td>Varebil</td></tr>
      <tr><td>Maks. pers.</td><td>2</td></tr>
      <tr><td>Ant. dører</td><td>5</td></tr>
      <tr><td>Min. sjåføralder</td><td>21</td></tr>
      <tr><td>Girtype</td><td>Manuell</td></tr>
      <tr><td>Klimaanlegg?</td><td>Ja</td></tr>
      <tr><td>Ubegrenset km?</td><td>Nei</td></tr>
    </table>
    <div class="btn">Book Now</div>
  </article>

  <article class="car-card" style="left:787px">
    <div class="car-photo" role="img" aria-label="Photo of a dark sedan at sunset" style="background:linear-gradient(180deg,#3a3f5a 0%,#b8706a 35%,#7a5a48 65%,#2a2320 100%)"></div>
    <h3>Varebilen</h3>
    <div class="price">Pris per døgn <b>kr 600</b></div>
    <hr>
    <table class="specs">
      <tr><td>Biltype</td><td>Varebil</td></tr>
      <tr><td>Maks. pers.</td><td>2</td></tr>
      <tr><td>Ant. dører</td><td>5</td></tr>
      <tr><td>Min. sjåføralder</td><td>21</td></tr>
      <tr><td>Girtype</td><td>Manuell</td></tr>
      <tr><td>Klimaanlegg?</td><td>Ja</td></tr>
      <tr><td>Ubegrenset km?</td><td>Nei</td></tr>
    </table>
    <div class="btn">Book Now</div>
  </article>
</section>

<section class="features">
  <div class="feature" style="left:137px;top:57px">
    <svg width="32" height="20" viewBox="0 0 32 20"><rect x="1" y="3" width="28" height="12" rx="2" fill="#d9a400"/><rect x="4" y="6" width="6" height="4" fill="#fff"/><rect x="12" y="6" width="6" height="4" fill="#fff"/><circle cx="8" cy="17" r="2.5" fill="#d9a400"/><circle cx="23" cy="17" r="2.5" fill="#d9a400"/></svg>
    <span>Van with driver</span></div>
  <div class="feature" style="left:400px;top:52px">
    <svg width="22" height="30" viewBox="0 0 22 30"><path d="M11 1C7 9 2 14 2 20a9 9 0 0 0 18 0c0-6-5-11-9-19z" fill="#d9a400"/></svg>
    <span>Moving Wash</span></div>
  <div class="feature" style="left:616px;top:44px">
    <svg width="28" height="24" viewBox="0 0 28 24"><rect x="1" y="5" width="26" height="18" rx="2" fill="#d9a400"/><rect x="9" y="1" width="10" height="5" fill="none" stroke="#d9a400" stroke-width="2"/><path d="M7 6v16M21 6v16" stroke="#fff" stroke-width="1.5"/></svg>
    <span>Collection / delivery<br>of goods</span></div>
  <div class="feature" style="left:892px;top:46px">
    <svg width="20" height="28" viewBox="0 0 20 28"><path d="M10 1a8 8 0 0 0-8 8c0 6 8 17 8 17s8-11 8-17a8 8 0 0 0-8-8z" fill="#d9a400"/><circle cx="10" cy="9" r="3" fill="#fff"/></svg>
    <span>Optional delivery<br>location</span></div>
</section>

<section class="video" role="img" aria-label="Video still of a black car front in a dark studio">
  <div class="play"><svg width="60" height="60"><path d="M24 18l18 12-18 12z" fill="#8a8a8a"/></svg></div>
</section>

<footer class="site-footer">
  <h4 style="left:102px">Quick Links</h4>
  <a href="#" style="left:104px;top:67px">Hjem</a>
  <a href="#" style="left:104px;top:92px">Bilparken vår</a>
  <a href="#" style="left:104px;top:117px">Tjenester</a>
  <a href="#" style="left:104px;top:142px">Kontakt oss</a>
  <a href="#" style="left:220px;top:67px">Blog</a>
  <a href="#" style="left:220px;top:92px">Page templates</a>
  <a href="#" style="left:220px;top:117px">About us</a>
  <div class="fsep" style="left:345px"></div>

  <h4 style="left:381px">Support Links</h4>
  <a href="#" style="left:384px;top:67px">Press</a>
  <a href="#" style="left:384px;top:92px">Legal Notice</a>
  <a href="#" style="left:384px;top:117px">Privacy Policy</a>
  <a href="#" style="left:384px;top:142px">Term of Use</a>
  <a href="#" style="left:498px;top:67px">Help</a>
  <a href="#" style="left:498px;top:92px">Contact</a>
  <div class="fsep" style="left:578px"></div>

  <h4 style="left:615px">Newsletters Sign Up</h4>
  <p class="news-text">Sign up for our daily email by entering your information below</p>
  <div class="email">Email address<span class="btn">SUBMIT</span></div>
  <div class="fsep" style="left:904px"></div>

  <h4 style="left:945px">Connect With Us</h4>
  <span class="social" style="left:943px;background:#3b5998"></span>
  <span class="social" style="left:983px;background:#33aaf0"></span>
  <span class="social" style="left:1024px;background:#dd4b39"></span>
  <span class="social" style="left:1065px;background:#d62e2a"></span>
</footer>

<div class="bottom-bar">Copyright © 2014 Solvikbyen Car. All rights reserved.</div>

</body>
</html>
```